Klassisches Visitenkarten-Design mit braunen Farbtönen gesucht
Zielgruppe
Meine Firma bietet Pferdezahnbehandlungen, Pferdefütterungsberatung sowie Trensen- und Gebissanpassungen an. Ausserdem habe ich eine mobile Pferdewaage. Meine Kunden sind Pferdebesitzer der gehobenen Klasse, die gerne Geld in die Hand nehmen um ihr Tier korrekt zu halten/versorgen.
Ich setze bisher auf ein klassisches Design in braun Tönen.
Aufgabenstellung
Mir ist eine klare, schnörkellose Botschaft wichtig.
Ich möchte mich gerne mit klassischem, aber auch sehr schönem Design von der Konkurrenz abheben.
Der Fokus soll auf der wissenschaftlichen Arbeitsweise mit dem Partner Pferd liegen.
Im Anhang sind Fotos von der alten Visitenkarten. Dort fehlt mir aber die klare Linie.
Normalerweise arbeite ich mit der Schriftart Eurostyle, bin aber auch für neue Vorschläge offen.

```html
<!DOCTYPE html>
<html lang="de">
<head>
<meta charset="utf-8">
<title>EQUIVETA – Visitenkarte</title>
<link rel="stylesheet" href="https://fonts.googleapis.com/css2?family=Saira:wght@400;700&display=swap">
<style>
  :root {
    --backdrop: #ededed;
    --card: #ffffff;
    --text-grey: #737373;
    --brown-dark: #552e12;
    --shadow-light: #b9bac0;
    --shadow-dark: #72777d;
  }
  html, body {
    margin: 0;
    padding: 0;
    width: 1200px;
    height: 1200px;
    overflow: hidden;
    background: var(--backdrop);
    font-family: "Saira", "Arial", sans-serif;
  }
  .card-wrap {
    position: absolute;
    left: 238px;
    width: 723px;
    height: 468px;
  }
  .card-wrap--front { top: 80px; }
  .card-wrap--back { top: 643px; }
  .card-shadow {
    position: absolute;
    left: 10px;
    top: 10px;
    width: 723px;
    height: 468px;
    background: linear-gradient(90deg, var(--shadow-light), var(--shadow-dark));
  }
  .card {
    position: absolute;
    inset: 0;
    background: var(--card);
    overflow: hidden;
  }
  .contact {
    position: absolute;
    left: 51px;
    top: 96px;
    color: var(--text-grey);
  }
  .contact__name {
    margin: 0;
    font-weight: 700;
    font-size: 27px;
    line-height: 32px;
  }
  .contact__role {
    margin: 20px 0 0;
    font-weight: 700;
    font-size: 21px;
    line-height: 24px;
  }
  .contact__block {
    margin: 25px 0 0;
    font-weight: 400;
    font-size: 22px;
    line-height: 24px;
  }
  .contact__block + .contact__block { margin-top: 23px; }
  .services {
    position: absolute;
    left: 51px;
    right: 58px;
    font-weight: 700;
    font-size: 18.5px;
    color: var(--text-grey);
    white-space: nowrap;
    word-spacing: 1px;
  }
  .card-wrap--front .services { top: 394px; }
  .card-wrap--back .services { top: 402px; left: 55px; right: 54px; text-align: center; }
  .brand-band {
    position: absolute;
    left: 0;
    right: 0;
    bottom: 0;
    height: 40px;
    background: var(--brown-dark);
  }
  .brand-mark {
    position: absolute;
    display: flex;
    align-items: center;
    justify-content: center;
    gap: 10px;
    font-weight: 700;
    color: var(--brown-dark);
    letter-spacing: 1px;
  }
  .brand-mark__dot {
    width: 16px;
    height: 16px;
    border-radius: 50%;
    background: var(--brown-dark);
  }
  .card-wrap--front .brand-mark {
    left: 441px;
    top: 34px;
    width: 224px;
    height: 350px;
    font-size: 34px;
  }
  .card-wrap--back .brand-mark {
    left: 200px;
    top: 34px;
    width: 323px;
    height: 348px;
    font-size: 44px;
  }
</style>
</head>
<body>

<section class="card-wrap card-wrap--front">
  <div class="card-shadow"></div>
  <div class="card">
    <div class="contact">
      <p class="contact__name">Marlene T. Vogt</p>
      <p class="contact__role">Agrarwissenschaften (Dr. sc.)<br>EQUIVETA</p>
      <p class="contact__block">Lindenweg 14<br>79999 Talheim/Hochschwarzwald</p>
      <p class="contact__block">Telefon: +49 (0) 160 - 5550184<br>E-Mail: kontakt@equiveta-zahn.com<br>Internet: www.equiveta.de</p>
    </div>
    <div class="brand-mark"><span class="brand-mark__dot"></span>EQUIVETA</div>
    <div class="services">Pferdezahnbehandlung &nbsp;*&nbsp; Pferdefütterungsberatung &nbsp;*&nbsp; Pferdewaage</div>
    <div class="brand-band"></div>
  </div>
</section>

<section class="card-wrap card-wrap--back">
  <div class="card-shadow"></div>
  <div class="card">
    <div class="brand-mark"><span class="brand-mark__dot"></span>EQUIVETA</div>
    <div class="services">Pferdezahnbehandlung &nbsp;*&nbsp; Pferdefütterungsberatung &nbsp;*&nbsp; Pferdewaage</div>
  </div>
</section>

</body>
</html>
```